Website Design for The Elder Nook

Please design and code a new website.
Here are the sites I like best:
http://www.voyaglint.com/alternate/
http://www.wheelgiftbay.org
Please make it similar but look at the competitor site (below) for images and wording. This is NOT a car donation site. It's a senior lead placement site like https://www.kinhavenfinder.com. I just like this sites above as a lead generation sites.
Competitor site:
https://www.kinhavenfinder.com (use ideas / verbiage from this site)
Updates
Competitor site:
Coding
Coded - Design and coding required
Number of Pages Required
1 page
Look and feel
Each slider illustrates characteristics of the customer's brand and the style your logo design should communicate.

```html
<!DOCTYPE html>
<html lang="en">
<head>
<meta charset="utf-8">
<title>The Elder Nook – Senior Living Advisors</title>
<link rel="stylesheet" href="https://fonts.googleapis.com/css2?family=Jost:ital,wght@0,300;0,400;0,500;1,400&family=Libre+Baskerville:ital@0;1&display=swap">
<style>
:root{
  --blue:#0d5eb1;
  --blue-dark:#0a4d93;
  --green:#7dc242;
  --ink:#222;
  --muted:#555;
  --line:#dcdcdc;
  --paper:#fff;
  --serif:"Libre Baskerville",Georgia,serif;
  --sans:"Jost",Arial,sans-serif;
}
*{box-sizing:border-box;margin:0;padding:0}
h1,h2,h3{font-weight:400}
html,body{width:1200px;height:3040px;overflow:hidden;background:var(--paper)}
body{position:relative;font-family:var(--sans);color:var(--ink)}
.abs{position:absolute}
.green{color:var(--green)}
.blue{color:var(--blue)}

/* header */
.brand{left:142px;top:22px;display:flex;align-items:center;gap:10px;font-family:var(--serif);font-size:24px;color:var(--blue)}
.brand-dot{width:30px;height:30px;border-radius:50%;background:var(--green)}
.contact{left:572px;top:24px;display:flex;align-items:center;gap:10px}
.contact small{display:block;font-family:var(--serif);font-size:11px;color:#444}
.contact strong{display:block;font-size:24px;font-weight:400;color:#222;line-height:1.1}
.badge{left:805px;top:22px;width:127px;height:49px;background:var(--blue);border-radius:3px}
.lang{left:957px;top:28px;width:102px;height:35px;border:1px solid var(--line);display:flex;align-items:center;justify-content:center;gap:8px;font-size:13px;color:#444}
.lang span.flag{width:32px;height:18px;background:linear-gradient(#b22 0 15%,#fff 15% 30%,#b22 30% 45%,#fff 45% 60%,#b22 60% 75%,#fff 75% 90%,#b22 90%)}

.nav{left:0;top:91px;width:1200px;height:42px;background:var(--blue)}
.nav ul{list-style:none;display:flex;margin-left:142px;height:100%}
.nav li{font-family:var(--serif);font-size:12px;color:#fff;padding:0 11px;display:flex;align-items:center;border-right:1px solid rgba(255,255,255,.25)}
.nav li.active{background:var(--blue-dark);border-bottom:3px solid var(--green)}

/* hero */
.hero{left:0;top:133px;width:1200px;height:573px;background:linear-gradient(90deg,#c9d3dc 0%,#e9ecef 35%,#d9dde2 60%,#e6e9ec 100%)}
.inquiry{left:694px;top:179px;width:364px;height:417px;background:#f7f7f7}
.inquiry h3{height:62px;background:var(--green);color:#fff;font-family:var(--serif);font-size:23px;display:flex;align-items:center;justify-content:center}
.field{position:absolute;left:29px;width:306px;height:42px;border:1px solid #ccc;background:#fff;display:flex;font-size:13px;color:#555}
.field i{width:40px;border-right:1px solid #ccc;display:flex;align-items:flex-start;justify-content:center;padding-top:13px;background:#fafafa}
.field span{padding:13px 16px}
.field i::before{content:"";width:11px;height:11px;background:#555;border-radius:2px}
.submit{position:absolute;left:29px;top:342px;width:306px;height:38px;background:var(--blue);color:#fff;font-family:var(--serif);font-size:14px;display:flex;align-items:center;justify-content:center;border-radius:2px}
.tagline{left:0;top:648px;width:1200px;text-align:center;font-family:var(--serif);font-size:27px;color:#111}
.tagline em{color:var(--blue)}

/* support */
.h2{font-family:var(--serif);font-size:28px;text-align:center;width:1200px;left:0}
.lede{left:205px;width:790px;text-align:center;font-size:14px;line-height:24px;color:#333}
.card{top:899px;width:171px;height:181px;border:1px solid #e3e3e3;box-shadow:0 4px 8px rgba(0,0,0,.08);text-align:center;padding:24px 16px 0;font-size:17px;line-height:21px;color:#333}
.card svg{display:block;margin:0 auto 10px}
.nocost{left:142px;top:1132px;font-family:var(--serif);font-size:23px}
.nocost-text{left:426px;top:1125px;font-size:17px;line-height:25px;color:#333}
.callnow{left:869px;top:1135px;font-size:22px;color:var(--blue)}

/* advisor band */
.advisor{left:0;top:1251px;width:1200px;height:480px;background:linear-gradient(90deg,#1b5fa8,#2a6fb8 50%,#1b5fa8)}
.advisor-head{left:0;top:1327px;width:1200px;text-align:center;color:#fff;font-family:var(--serif);font-size:28px}
.advisor-lede{left:0;top:1376px;width:1200px;text-align:center;color:#fff;font-size:15px}
.perk{top:1425px;width:190px;text-align:center;color:#fff;font-size:16px;line-height:20px}
.perk .ring{width:97px;height:97px;border:1.5px solid #fff;border-radius:50%;margin:0 auto 18px;display:flex;align-items:center;justify-content:center}
.search{left:298px;top:1601px;width:604px;height:45px;background:#fff;border-radius:2px;display:flex;align-items:center;padding:0 4px 0 20px;font-size:15px;color:#333}
.search b{margin-left:auto;font-family:var(--serif);font-weight:400;background:var(--green);color:#fff;font-size:15px;width:222px;height:37px;display:flex;align-items:center;justify-content:center}

/* testimonials */
.quote{top:1870px;width:284px;height:148px;border:1px solid #e3e3e3;padding:14px 17px;font-size:13px;line-height:22px;color:#666;letter-spacing:.2px}
.avatar{top:1995px;width:70px;height:70px;border-radius:50%;border:3px solid var(--blue);background:linear-gradient(#e4d7c7,#c7b39c)}
.who{top:2028px;font-family:var(--serif);font-size:14px;color:#333}
.btn{background:var(--green);color:#fff;font-family:var(--serif);font-size:15px;display:flex;align-items:center;justify-content:center;border-radius:2px}

/* veterans */
.vets{left:0;top:2215px;width:1200px;height:291px;background:linear-gradient(135deg,#1a2140 0%,#3a1c24 45%,#201a1c 75%,#111 100%)}
.vets-head{left:0;top:2285px;width:1200px;text-align:center;color:#fff;font-family:var(--serif);font-size:24px}
.vets-text{left:0;top:2328px;width:1200px;text-align:center;color:#fff;font-size:14px;line-height:24px}

/* states */
.states{top:2639px;list-style:none;font-size:13px;line-height:21.8px;color:#333}
.states li::before{content:"› "}

/* footer */
.footer{left:0;top:2871px;width:1200px;height:169px;background:var(--blue)}
.footer-nav{left:0;top:2920px;width:1200px;display:flex;justify-content:center;gap:33px;font-family:var(--serif);font-size:11px;color:#fff}
.footer-rule{left:142px;top:2985px;width:916px;height:1px;background:rgba(255,255,255,.35)}
.copy{left:142px;top:3002px;color:#fff;font-size:13px}
.social{top:2999px;width:24px;height:24px;border-radius:50%;border:1.5px solid #fff;background:var(--blue-dark)}
</style>
</head>
<body>

<header>
  <div class="abs brand"><span class="brand-dot"></span>The Elder Nook</div>
  <div class="abs contact">
    <svg width="34" height="34" viewBox="0 0 24 24" fill="none" stroke="#0d5eb1" stroke-width="1.5"><path d="M5 3h4l2 5-2.5 1.5a11 11 0 0 0 6 6L16 13l5 2v4a2 2 0 0 1-2 2A16 16 0 0 1 3 5a2 2 0 0 1 2-2z"/></svg>
    <div><small>Talk to a local advisor for FREE</small><strong>(555) 014-2983</strong></div>
  </div>
  <div class="abs badge" role="img" aria-label="Accreditation badge"></div>
  <div class="abs lang">EN : <span class="flag"></span> ⌄</div>
</header>

<nav class="abs nav">
  <ul>
    <li class="active">ASSISTED LIVING</li><li>MEMORY CARE</li><li>NURSING HOMES</li><li>MORE LIVING OPTIONS ⌄</li><li>PLANNING &amp; ADVICE</li><li>HOW OUR SERVICE WORKS</li>
  </ul>
</nav>

<section>
  <div class="abs hero" role="img" aria-label="Photo of an advisor reviewing paperwork with a senior couple"></div>
  <form class="abs inquiry">
    <h3>Quick Inquiry</h3>
    <div class="field" style="top:91px"><i></i><span>Name</span></div>
    <div class="field" style="top:144px"><i></i><span>Phone</span></div>
    <div class="field" style="top:198px"><i></i><span>Email</span></div>
    <div class="field" style="top:252px;height:70px"><i></i><span>Message</span></div>
    <div class="submit">Submit Now</div>
  </form>
  <p class="abs tagline">You know your family.We know <em>Senior Living.</em></p>
</section>

<section>
  <h2 class="abs h2" style="top:782px"><span class="green">The Support You Need To</span> <span class="blue">Make The Right Choice</span></h2>
  <p class="abs lede" style="top:828px">Lorem ipsum dolor sit amet, consectetuer adipiscing elit, sed diam nonummy nibh euismod tincidunt ut laoreet dolore magna aliquam erat volutpat. Ut wisi enim ad minim veniam, quis nostrud exerci tation ullamcorper suscipit.</p>

  <div class="abs card" style="left:142px">
    <svg width="50" height="56" viewBox="0 0 50 56" fill="none" stroke="#7dc242" stroke-width="2"><circle cx="25" cy="14" r="9"/><path d="M8 54V36a10 10 0 0 1 10-10h14a10 10 0 0 1 10 10v18M25 26v28M19 26l6 8 6-8"/></svg>
    Dedicated local<br>advisor</div>
  <div class="abs card" style="left:328px">
    <svg width="50" height="56" viewBox="0 0 50 56" fill="none" stroke="#7dc242" stroke-width="2"><path d="M3 26L25 5l22 21M9 21v33h32V21M20 54V40h10v14M21 24h8v8h-8z"/></svg>
    Hand-picked list of<br>communities to<br>match your needs</div>
  <div class="abs card" style="left:514px">
    <svg width="50" height="56" viewBox="0 0 50 56" fill="none" stroke="#7dc242" stroke-width="2"><circle cx="27" cy="22" r="10"/><path d="M27 16v12M24 19h5a2 2 0 0 1 0 4h-4a2 2 0 0 0 0 4h5M27 2v5M20 4l2 4M34 4l-2 4M4 40l10-4h10l6 3h-10M4 52l12-2 24-10"/></svg>
    Full details and<br>pricing</div>
  <div class="abs card" style="left:700px">
    <svg width="50" height="56" viewBox="0 0 50 56" fill="none" stroke="#7dc242" stroke-width="2"><rect x="2" y="8" width="46" height="44"/><path d="M2 18h46M12 3v10M38 3v10M10 26h30v18H10zM20 26v18M30 26v18M10 35h30"/></svg>
    Help scheduling<br>tours</div>
  <div class="abs card" style="left:886px">
    <svg width="62" height="56" viewBox="0 0 62 56" fill="none" stroke="#7dc242" stroke-width="2"><path d="M14 12h26v28H14zM40 20h10l8 10v10H40M4 18h8M2 26h10M6 34h6"/><circle cx="22" cy="44" r="5"/><circle cx="48" cy="44" r="5"/></svg>
    Move in<br>support</div>

  <p class="abs nocost"><span class="green">There's</span> <span class="blue">No Cost To You.</span></p>
  <p class="abs nocost-text">We work with over 20,000 senior living communities.<br>Our community partners pay us for placement services.</p>
  <p class="abs callnow">Call (555) 014-2983</p>
</section>

<section>
  <div class="abs advisor" role="img" aria-label="Blue-tinted portraits of local senior living advisors"></div>
  <h2 class="abs advisor-head">Your local advisor informs. You decide.</h2>
  <p class="abs advisor-lede">Lorem ipsum dolor sit amet, consectetuer adipiscing elit, sed diam nonummy nibh euismod tincidunt ut laoreet.</p>
  <div class="abs perk" style="left:245px">
    <div class="ring"><svg width="34" height="56" viewBox="0 0 34 56" fill="none" stroke="#fff" stroke-width="1.8"><circle cx="17" cy="14" r="11"/><path d="M17 25v30"/></svg></div>
    Insider's tips for the area near you</div>
  <div class="abs perk" style="left:505px">
    <div class="ring"><svg width="54" height="48" viewBox="0 0 54 48" fill="none" stroke="#fff" stroke-width="1.8"><path d="M27 45L6 24A12 12 0 0 1 27 8a12 12 0 0 1 21 16z"/></svg></div>
    Advice tailored to your unique situation</div>
  <div class="abs perk" style="left:766px">
    <div class="ring"><svg width="52" height="44" viewBox="0 0 52 44" fill="none" stroke="#fff" stroke-width="1.8"><circle cx="5" cy="6" r="4"/><circle cx="5" cy="22" r="4"/><circle cx="5" cy="38" r="4"/><path d="M16 6h34M16 22h34M16 38h34"/></svg></div>
    Time saving know-how and resources</div>
  <div class="abs search">Enter city or postal code<b>Find an advisor near you</b></div>
</section>

<section>
  <h2 class="abs h2" style="top:1809px"><span class="green">93% Of Our Customers</span> <span class="blue">Recommend Our Service</span></h2>

  <p class="abs quote" style="left:142px">Lorem ipsum dolor sit amet, consectetuer adipiscing elit, sed diam nonummy nibh euismod tincidunt ut laoreet dolore magna aliquam erat volutpat. Ut wisi enim ad minim veniam, quis nostrud.</p>
  <div class="abs avatar" style="left:151px" role="img" aria-label="Customer portrait"></div>
  <p class="abs who" style="left:242px">Dana Hollis</p>

  <p class="abs quote" style="left:458px">Lorem ipsum dolor sit amet, consectetuer adipiscing elit, sed diam nonummy nibh euismod tincidunt ut laoreet dolore magna aliquam erat volutpat. Ut wisi enim ad minim veniam, quis nostrud.</p>
  <div class="abs avatar" style="left:467px" role="img" aria-label="Customer portrait"></div>
  <p class="abs who" style="left:559px">Owen Brandt</p>

  <p class="abs quote" style="left:774px">Lorem ipsum dolor sit amet, consectetuer adipiscing elit, sed diam nonummy nibh euismod tincidunt ut laoreet dolore magna aliquam erat volutpat. Ut wisi enim ad minim veniam, quis nostrud.</p>
  <div class="abs avatar" style="left:784px" role="img" aria-label="Customer portrait"></div>
  <p class="abs who" style="left:875px">Mara Quinn</p>

  <div class="abs btn" style="left:496px;top:2092px;width:208px;height:38px">See More Testimonials</div>
</section>

<section>
  <div class="abs vets" role="img" aria-label="Waving American flag in dark light"></div>
  <h2 class="abs vets-head">Access Up To $2,000 Per Month In Veteran's Aid</h2>
  <p class="abs vets-text">We work with Veterans every day. Most veteran families do not know of a key benefit available to them and their families.<br>It's called the Veteran's Aid and Attendance benefit. This benefit can help pay for senior living and home care.</p>
  <div class="abs btn" style="left:535px;top:2392px;width:130px;height:37px">Learn More</div>
</section>

<section>
  <h2 class="abs h2" style="top:2584px"><span class="green">Senior Assisted</span> <span class="blue">Living by State</span></h2>
  <ul class="abs states" style="left:159px"><li>Alabama</li><li>Arizona</li><li>Arkansas</li><li>California</li><li>Colorado</li><li>Connecticut</li><li>Delaware</li></ul>
  <ul class="abs states" style="left:301px"><li>District of Columbia</li><li>Florida</li><li>Georgia</li><li>Hawaii</li><li>Idaho</li><li>Illinois</li><li>Indiana</li></ul>
  <ul class="abs states" style="left:486px"><li>Iowa</li><li>Kansas</li><li>Kentucky</li><li>Louisiana</li><li>Maine</li><li>Maryland</li><li>Massachusetts</li></ul>
  <ul class="abs states" style="left:644px"><li>Michigan</li><li>Minnesota</li><li>Mississippi</li><li>Missouri</li><li>Montana</li><li>Nebraska</li><li>Nevada</li></ul>
  <ul class="abs states" style="left:780px"><li>New Hampshire</li><li>New Jersey</li><li>New Mexico</li><li>New York</li><li>North Carolina</li><li>North Dakota</li><li>Ohio</li></ul>
  <ul class="abs states" style="left:950px"><li>Oklahoma</li><li>Oregon</li><li>Pennsylvania</li><li>Rhode Island</li><li>South Carolina</li><li>South Dakota</li><li>Tennessee</li></ul>
</section>

<footer>
  <div class="abs footer"></div>
  <div class="abs footer-nav"><span>ASSISTED LIVING</span><span>MEMORY CARE</span><span>NURSING HOMES</span><span>MORE LIVING OPTIONS ⌄</span><span>PLANNING &amp; ADVICE</span><span>HOW OUR SERVICE WORKS</span></div>
  <div class="abs footer-rule"></div>
  <p class="abs copy">Copyright 2019 The Elder Nook. All Rights Reserved.</p>
  <span class="abs social" style="left:946px"></span>
  <span class="abs social" style="left:976px"></span>
  <span class="abs social" style="left:1005px"></span>
  <span class="abs social" style="left:1034px"></span>
</footer>

</body>
</html>
```